Oil Field Service company needs professional business cards

Looking to clean up our current company business cards and look a little more professional. Brenwick Casing Services is a US based company that services the oil field. We deal with engineers, managers and oil rigs....................................................................................................................................................................................................................................................................................................................................................................................................

Target Market(s)

Oil and Gas professionals

Industry/Entity Type

Oil And Gas

Contact Information for Business Card

See attached photo as example

Font styles to use
Sans Serif

Colors
ec1f27

Requirements
Must have
• Company Logo, Name, Title, Cell, Office, Fax, Email.
• See attached photo
Nice to have
• External CRT, Internal CRT, Casing Crews, Torque Turn, Laydown Machine
Should not have
• Do not introduce any new pictures and keep it professional looking

```html
<!DOCTYPE html>
<html lang="en">
<head>
<meta charset="utf-8">
<title>Brenwick Casing Services – Business Card</title>
<link rel="stylesheet" href="https://fonts.googleapis.com/css2?family=Open+Sans:wght@400;600;700;800&display=swap">
<style>
  :root {
    --slate: #434f5b;
    --slate-dark: #37414b;
    --red: #ec1f27;
    --white: #ffffff;
    --ink: #4a5460;
    --muted: #dfe3e7;
    --backdrop: #e9e6e1;
  }
  * { box-sizing: border-box; margin: 0; padding: 0; }
  html, body { width: 1200px; height: 950px; overflow: hidden; }
  body {
    background: var(--backdrop);
    font-family: "Open Sans", Arial, sans-serif;
    position: relative;
  }
  .card {
    position: absolute;
    width: 700px;
    height: 400px;
    border-radius: 4px;
    overflow: hidden;
    box-shadow: 0 10px 28px rgba(0,0,0,.22);
  }
  /* Front */
  .card-front { left: 90px; top: 50px; background: var(--white); }
  .front-contact {
    height: 225px;
    background: var(--slate);
    color: var(--white);
    display: flex;
    justify-content: space-between;
    padding: 40px 48px 0 48px;
  }
  .holder-name { font-size: 30px; font-weight: 700; letter-spacing: .2px; }
  .holder-title { font-size: 17px; color: var(--muted); margin-top: 2px; }
  .contact-list { list-style: none; font-size: 17px; line-height: 27px; color: var(--muted); }
  .contact-list li { display: flex; align-items: center; gap: 10px; }
  .contact-list svg { width: 16px; height: 16px; fill: var(--muted); flex: none; }
  .contact-list .address { margin-bottom: 6px; padding-left: 26px; }
  .contact-list .web { padding-left: 26px; letter-spacing: 3px; margin-top: 4px; }
  .divider { height: 4px; background: var(--red); }
  .front-brand {
    height: 171px;
    display: flex;
    align-items: center;
    justify-content: center;
    gap: 14px;
  }
  .brand-mark { width: 22px; height: 22px; border-radius: 50%; background: var(--red); flex: none; }
  .brand-name {
    font-size: 30px; font-weight: 800; color: var(--ink);
    letter-spacing: 1px; text-transform: uppercase;
  }
  /* Back */
  .card-back {
    left: 410px; top: 500px; background: var(--slate);
    color: var(--white);
    display: flex; flex-direction: column; justify-content: center; align-items: center;
    gap: 44px;
  }
  .card-back .brand-name { color: var(--white); font-size: 34px; }
  .card-back .brand-mark { width: 24px; height: 24px; }
  .brand-lockup { display: flex; align-items: center; gap: 16px; }
  .service-list { text-align: center; font-size: 19px; line-height: 30px; color: var(--white); }
</style>
</head>
<body>
  <section class="card card-front" aria-label="Business card front">
    <div class="front-contact">
      <div class="holder">
        <p class="holder-name">Carl Hendry</p>
        <p class="holder-title">Area Manager</p>
      </div>
      <ul class="contact-list">
        <li class="address">Alder Creek, OK 73000</li>
        <li>
          <svg viewBox="0 0 16 16" aria-label="Office"><path d="M3 1h3l1.5 4-2 1.5a9 9 0 0 0 4 4L11 8.5l4 1.5v3a2 2 0 0 1-2 2A12 12 0 0 1 1 3a2 2 0 0 1 2-2z"/></svg>
          (555)210-4400
        </li>
        <li>
          <svg viewBox="0 0 16 16" aria-label="Cell"><path d="M4 0h8a1 1 0 0 1 1 1v14a1 1 0 0 1-1 1H4a1 1 0 0 1-1-1V1a1 1 0 0 1 1-1zm1 2v10h6V2zm3 11a1 1 0 1 0 0 2 1 1 0 0 0 0-2z"/></svg>
          (555)318-2261
        </li>
        <li>
          <svg viewBox="0 0 16 16" aria-label="Fax"><path d="M4 0h8v5H4zM1 6h14v7h-3v3H4v-3H1zm4 5v4h6v-4z"/></svg>
          (555)210-4410
        </li>
        <li>
          <svg viewBox="0 0 16 16" aria-label="Email"><path d="M0 3h16v10H0zm1.5 1.2V12h13V4.2L8 9z"/></svg>
          carl@brenwick.com
        </li>
        <li class="web">www.brenwick.com</li>
      </ul>
    </div>
    <div class="divider"></div>
    <div class="front-brand">
      <span class="brand-mark"></span>
      <span class="brand-name">Brenwick Casing Services</span>
    </div>
  </section>

  <section class="card card-back" aria-label="Business card back">
    <div class="brand-lockup">
      <span class="brand-mark"></span>
      <span class="brand-name">Brenwick Casing Services</span>
    </div>
    <p class="service-list">
      External CRT • Internal CRT • Casing Crews<br>
      Torque Turn • Laydown Machine
    </p>
  </section>
</body>
</html>
```